tinyTally Resource Book - 10 maths tasks to do outside

I need a 22 (11 pages back to back) page A6 sized book produced to standard for submission to professional printer. Needs to be as .pdf file showing guide lines and allowances for colour bleed. I have text already written and submitted as attachment in a Word file with margins set to A6 size. The theme of the materials is "Nature Play" so using lots of pictures from nature (Australia preferably) and showing lots of patterns in nature (rocks, leaves, flower petals etc). Some of the tasks refer to specific activities, such as "shadows" and "floating" so would be great to illustrate appropriately. The big emphasis is on learning outside the classroom, getting kids to engage actively with nature. I would like to see the pages as full colour - so not white background. The book itself will be spiral bound along the top edge so a margin of at least 1cm will be required at the top of each page (or the bottom of even numbered pages). Book will be printed on plastic laminated matte paper for outdoor use. Font size needs to be big enough to read. Fonts sizes, alignments and page numbers are all different at the moment and need to be standardised. One photo is included in a page as a sample if you can use it, otherwise disregard. Logo for Wattlebrook Numeracy Guild is also included to have as part of the acknowledgements at the back of the book.

Target Market(s)

Book is for early childhood and preschool teachers.

Industry/Entity Type

Education

Font styles to use
Sans Serif

Requirements
Must have
• Colour and appeal.
Nice to have
• Use of natural colours instead of bright catchy colours but that is your call.
Should not have
• American spelling

```html
<!DOCTYPE html>
<html lang="en-AU">
<head>
<meta charset="utf-8">
<title>tinyTally Resource Book – Task 1: How Many Leaves?</title>
<link rel="stylesheet" href="https://fonts.googleapis.com/css2?family=Fredoka:wght@700&family=Questrial&display=swap">
<style>
  :root {
    --paper: #ffffff;
    --crop: #1a1a1a;
    --heading-fill: #f7a81b;
    --heading-stroke: #e2231a;
    --bullet: #2b3990;
    --body-text: #1f2140;
    --leaf-green: #b7c98a;
    --leaf-lime: #dfe59a;
    --leaf-maroon: #a8707a;
    --leaf-rose: #e6a3a3;
    --leaf-olive: #8fa06a;
    --leaf-plum: #9c6f86;
  }
  * { margin: 0; padding: 0; box-sizing: border-box; }
  html, body { width: 906px; height: 1200px; overflow: hidden; background: var(--paper); }
  .sheet { position: relative; width: 906px; height: 1200px; }

  .nature-backdrop {
    position: absolute; left: 52px; top: 52px; width: 802px; height: 1099px;
    background:
      radial-gradient(ellipse 260px 180px at 18% 12%, var(--leaf-maroon), transparent 70%),
      radial-gradient(ellipse 240px 200px at 80% 20%, var(--leaf-lime), transparent 70%),
      radial-gradient(ellipse 280px 220px at 30% 45%, var(--leaf-lime), transparent 70%),
      radial-gradient(ellipse 260px 200px at 78% 50%, var(--leaf-plum), transparent 70%),
      radial-gradient(ellipse 220px 180px at 12% 68%, var(--leaf-green), transparent 70%),
      radial-gradient(ellipse 260px 220px at 55% 75%, var(--leaf-maroon), transparent 70%),
      radial-gradient(ellipse 240px 200px at 88% 85%, var(--leaf-lime), transparent 70%),
      radial-gradient(ellipse 240px 200px at 20% 92%, var(--leaf-olive), transparent 70%),
      radial-gradient(ellipse 200px 160px at 60% 30%, var(--leaf-rose), transparent 70%),
      var(--leaf-green);
  }
  .nature-backdrop::after {
    content: ""; position: absolute; inset: 0;
    background: rgba(255, 255, 255, 0.42);
  }

  .crop-marks { position: absolute; inset: 0; width: 906px; height: 1200px; }
  .crop-marks line { stroke: var(--crop); stroke-width: 1.2; }

  .task-title, .section-heading {
    position: absolute; left: 129px;
    font-family: "Fredoka", sans-serif; font-weight: 700;
    color: var(--heading-fill);
    -webkit-text-stroke: 5px var(--heading-stroke);
    paint-order: stroke fill;
    letter-spacing: 0.5px;
  }
  .task-title { top: 128px; font-size: 50px; line-height: 56px; }
  .section-heading { font-size: 39px; line-height: 44px; }

  .point-list {
    position: absolute; left: 194px; list-style: none;
    font-family: "Questrial", sans-serif; font-size: 26px; line-height: 35.6px;
    color: var(--body-text);
  }
  .point-list li { position: relative; padding-left: 27px; }
  .point-list li::before {
    content: ""; position: absolute; left: 2px; top: 12px;
    width: 12px; height: 12px; background: var(--bullet);
    transform: rotate(45deg);
  }
</style>
</head>
<body>
<div class="sheet">
  <div class="nature-backdrop" role="img" aria-label="Full-bleed photograph of scattered autumn leaves in soft green, yellow, rose and maroon tones, faded behind the text"></div>

  <svg class="crop-marks" viewBox="0 0 906 1200" aria-hidden="true">
    <line x1="52" y1="0" x2="52" y2="36"/><line x1="0" y1="52" x2="36" y2="52"/>
    <line x1="72" y1="0" x2="72" y2="36"/><line x1="0" y1="72" x2="36" y2="72"/>
    <line x1="854" y1="0" x2="854" y2="36"/><line x1="870" y1="52" x2="906" y2="52"/>
    <line x1="834" y1="0" x2="834" y2="36"/><line x1="870" y1="72" x2="906" y2="72"/>
    <line x1="52" y1="1164" x2="52" y2="1200"/><line x1="0" y1="1151" x2="36" y2="1151"/>
    <line x1="72" y1="1164" x2="72" y2="1200"/><line x1="0" y1="1131" x2="36" y2="1131"/>
    <line x1="854" y1="1164" x2="854" y2="1200"/><line x1="870" y1="1151" x2="906" y2="1151"/>
    <line x1="834" y1="1164" x2="834" y2="1200"/><line x1="870" y1="1131" x2="906" y2="1131"/>
  </svg>

  <h1 class="task-title">1. How Many Leaves?</h1>
  <ul class="point-list" style="top:193px">
    <li>Get a collection of leaves</li>
    <li>Draw a 20cm x 20cm square (approx.)<br>on the ground</li>
    <li>Find how many of the leaves it takes to<br>cover the square</li>
  </ul>

  <h2 class="section-heading" style="top:416px">Prompting questions</h2>
  <ul class="point-list" style="top:463px">
    <li>Will it be the same if I change the way<br>I arrange the leaves? Try several differ-<br>ent arrangements.</li>
  </ul>

  <h2 class="section-heading" style="top:612px">Variations</h2>
  <ul class="point-list" style="top:656px">
    <li>Change the types of leaves used</li>
    <li>Change the size of the box</li>
    <li>Use bodies to measure big spaces</li>
  </ul>

  <h2 class="section-heading" style="top:808px">Big Ideas</h2>
  <ul class="point-list" style="top:854px">
    <li>Area</li>
    <li>Measure</li>
    <li>Count</li>
    <li>Space</li>
  </ul>
</div>
</body>
</html>
```